Telecommunications/Power civil contractor needs business card design

Were a new telecommunications/power underground civil contractor that is looking for a new business card design. Our company colours are silver or grey and orange. Feel free to use the white background logo or the black background logo.

Target Market(s)

Local contractors, utility companies, private sector mining/energy companies, developers.

Industry/Entity Type

Telecommunications

Contact Information for Business Card

Each card will need the following info:
Persons name:
Title:
E-mail:
Phone number:
Shop Address:
Mailing Address:

Requirements
Must have
• Each card will need the following info:
• Persons name:
• Title:
• E-mail:
• Phone number:
• Shop Address:
• Mailing Address:

```html
<!DOCTYPE html>
<html lang="en">
<head>
<meta charset="utf-8">
<title>Ridgeway Lines Contracting Inc – Business Card</title>
<link rel="stylesheet" href="https://fonts.googleapis.com/css2?family=Lato:wght@400;700;900&display=swap">
<style>
  :root {
    --page-bg: #d9dcdf;
    --card-bg: #eef0f1;
    --accent: #d8401c;
    --accent-dark: #c2361a;
    --ink: #2f3133;
    --ink-soft: #3c3e40;
    --rule: #4a4c4e;
  }
  * { margin: 0; padding: 0; box-sizing: border-box; }
  html, body {
    width: 1200px; height: 970px; overflow: hidden;
    background: var(--page-bg);
    font-family: "Lato", sans-serif;
  }
  .canvas { position: relative; width: 1200px; height: 970px; }
  .business-card {
    position: absolute; left: 100px; top: 185px;
    width: 1000px; height: 600px;
    background: var(--card-bg);
    box-shadow: 0 10px 30px rgba(0,0,0,0.18);
  }
  .band { position: absolute; left: 0; right: 0; height: 11px; background: var(--accent); }
  .band--top { top: 0; }
  .band--bottom { bottom: 0; background: var(--accent-dark); }

  .brand {
    position: absolute; left: 50px; top: 110px; width: 370px;
    display: flex; flex-direction: column; align-items: center;
  }
  .brand__dot { width: 150px; height: 150px; border-radius: 50%; background: var(--accent); }
  .brand__name {
    margin-top: 34px; text-align: center;
    font-weight: 900; color: var(--ink-soft);
    font-size: 34px; line-height: 1.05; letter-spacing: 1px; text-transform: uppercase;
  }
  .brand__name span { display: block; font-size: 20px; letter-spacing: 3px; }

  .divider {
    position: absolute; left: 474px; top: 130px; width: 2px; height: 270px;
    background: var(--rule);
  }

  .person { position: absolute; left: 547px; top: 192px; }
  .person__name { font-weight: 700; font-size: 30px; color: var(--accent); }
  .person__title { margin-top: 4px; font-size: 23px; color: var(--ink); }

  .contact { position: absolute; left: 547px; top: 302px; list-style: none; }
  .contact__item {
    display: flex; align-items: center; gap: 16px;
    font-size: 22px; color: var(--ink); height: 34px; margin-bottom: 14px;
  }
  .contact__icon { width: 24px; height: 24px; fill: var(--accent); flex: none; }

  .addresses { position: absolute; left: 163px; top: 486px; font-size: 24px; color: var(--ink); }
  .address { display: flex; height: 37px; align-items: center; }
  .address__label {
    font-weight: 700; color: var(--accent);
    border-bottom: 2px solid var(--accent); width: 203px; margin-right: 0;
  }
  .address__label--shop { width: 174px; margin-right: 29px; }
  .address__value { margin-left: 6px; }
</style>
</head>
<body>
<div class="canvas">
  <article class="business-card">
    <div class="band band--top"></div>

    <div class="brand">
      <div class="brand__dot"></div>
      <div class="brand__name">Ridgeway Lines<span>Contracting Inc</span></div>
    </div>

    <div class="divider"></div>

    <div class="person">
      <h1 class="person__name">Daniel Hartwell</h1>
      <p class="person__title">Chief Operating Officer</p>
    </div>

    <ul class="contact">
      <li class="contact__item">
        <svg class="contact__icon" viewBox="0 0 24 24" aria-hidden="true">
          <path d="M3 9c0-3 4-5 9-5s9 2 9 5v1.5h-4.5V8.5c-1-.6-2.6-1-4.5-1s-3.5.4-4.5 1v2H3z"/>
          <path d="M6 12h12l2 8H4z"/>
        </svg>
        412-555-0186
      </li>
      <li class="contact__item">
        <svg class="contact__icon" viewBox="0 0 24 24" aria-hidden="true">
          <path d="M2 5h20v14H2z M4 7v.4l8 5.6 8-5.6V7z" fill-rule="evenodd"/>
        </svg>
        enquiries@ridgewaylines.com
      </li>
    </ul>

    <div class="addresses">
      <p class="address"><span class="address__label">Mailing Address:</span><span class="address__value">88 Alder Lane, Pittsfield, PA 15200</span></p>
      <p class="address"><span class="address__label address__label--shop">Shop Address:</span><span class="address__value">#1450 Harlow Avenue, Brookdale, New York</span></p>
    </div>

    <div class="band band--bottom"></div>
  </article>
</div>
</body>
</html>
```